Brand new redesign of Brightpath finance website

I need a new website design that i can advertise a great low interest rate on the front page and capture input application details that will send through to my email address.

some car finance companies will be similar to this would be listed below

tallowcredit.example.com.au
mirabelfinance.example.com.au
finance725.example.com.au
quenbyfinance.example.com.au
finance91.example.com.au

Reason: I have changed the project to a committed project. all the webpages should have the same format just different content and i want to be able to edit the front page easily to update my interest rates.

Target Market(s)

Australian Finance market targeting a younger demographic

Industry/Entity Type

Finance

Coding

Coded - Design and coding required

Number of Pages Required

5+ page

Font styles to use
Serif
Sans Serif

Colors
0255a3
ffffff
cedeed

Requirements
Must have
• application capture form
• apply now buttons
• Headline rate front page

```html
<!DOCTYPE html>
<html lang="en">
<head>
<meta charset="utf-8">
<title>Brightpath Finance</title>
<link rel="stylesheet" href="https://fonts.googleapis.com/css2?family=Lato:ital,wght@0,400;0,700;0,900;1,400&family=Questrial&display=swap">
<style>
:root{
  --blue:#0255a3;
  --blue-dark:#023f7c;
  --pale:#cedeed;
  --white:#ffffff;
  --ink:#222222;
  --text:#333333;
  --grey-bg:#f1f1f1;
  --footer-bottom:#222222;
  --line:#c9c9c9;
}
*{box-sizing:border-box;margin:0;padding:0}
html,body{width:1200px;height:2228px;overflow:hidden}
body{font-family:"Lato",sans-serif;color:var(--text);background:var(--white);position:relative}
.wrap{position:absolute;left:162px;width:876px}

/* header */
.site-header{position:absolute;top:0;left:0;width:1200px;height:88px;border-top:3px solid #d8d8d8;background:var(--white)}
.brand{position:absolute;left:162px;top:18px;display:flex;align-items:center;gap:12px}
.brand-dot{width:56px;height:56px;border-radius:50%;background:var(--blue)}
.brand-name{font-family:"Lato",sans-serif;font-weight:900;font-size:30px;color:var(--blue);letter-spacing:.5px}
.apply-btn{position:absolute;left:745px;top:32px;width:116px;height:30px;background:var(--blue);color:var(--white);font-size:12px;font-weight:900;letter-spacing:.5px;display:flex;align-items:center;justify-content:center;border-left:3px solid var(--blue-dark);border-right:3px solid var(--blue-dark)}
.header-phone{position:absolute;left:890px;top:32px;display:flex;align-items:center;gap:10px;font-size:20px;font-weight:700;color:var(--blue)}

/* nav */
.main-nav{position:absolute;top:88px;left:0;width:1200px;height:46px;background:var(--blue)}
.main-nav ul{list-style:none;position:absolute;left:162px;top:0;display:flex;height:46px}
.main-nav li{font-size:14px;color:var(--white);text-transform:uppercase;display:flex;align-items:center;padding:0 15.5px}
.main-nav li.is-active{background:var(--pale);color:var(--text);padding:0 23px;position:relative}
.main-nav li.is-active::after{content:"";position:absolute;left:50%;bottom:0;margin-left:-6px;border:6px solid transparent;border-bottom-color:var(--blue);border-top:0}

/* hero */
.hero{position:absolute;top:134px;left:0;width:1200px;height:509px}
.hero-photo{position:absolute;inset:0;background:linear-gradient(100deg,#c9ced6 0%,#e5e8ec 30%,#b8bec8 55%,#d9dce1 75%,#a9aeb8 100%)}
.rate-list{position:absolute;left:373px;top:328px;width:340px;list-style:none}
.rate-list li{background:rgba(206,222,237,.92);border-radius:3px;margin-bottom:4px;padding:6px 10px 6px 34px;font-size:15px;color:var(--ink);text-transform:uppercase;line-height:27px;position:relative}
.rate-list svg{position:absolute;left:9px;top:11px}
.quote-panel{position:absolute;left:741px;top:0;width:297px;height:509px;background:var(--pale);padding:38px 15px 0 15px}
.quote-title{background:var(--blue);color:var(--white);font-size:17px;text-align:center;height:36px;line-height:36px;margin-bottom:20px}
.quote-field{height:38px;background:var(--white);margin-bottom:20px;font-size:12px;font-style:italic;color:#444;padding:0 8px;line-height:38px}
.quote-terms{font-size:13px;color:var(--text);display:flex;align-items:center;gap:6px;margin:-4px 0 22px 0}
.quote-terms span.box{width:9px;height:9px;border:1px solid #888;background:var(--white)}
.quote-terms a{color:var(--blue);text-decoration:none}
.quote-submit{margin:0 5px;height:50px;background:var(--blue);color:var(--white);font-size:16px;font-weight:900;letter-spacing:.3px;text-transform:uppercase;display:flex;align-items:center;justify-content:center;border-left:3px solid var(--blue-dark);border-right:3px solid var(--blue-dark)}

/* section headings */
.section-title{font-family:"Questrial",sans-serif;font-size:30px;text-align:center;color:var(--ink)}
.divider{position:relative;width:466px;height:30px;margin:10px auto 0}
.divider::before{content:"";position:absolute;left:0;right:0;top:15px;border-top:1px solid var(--line)}
.divider span{position:absolute;left:50%;top:6px;margin-left:-9px;width:18px;height:18px;border-radius:50%;background:var(--blue)}

/* pre approval */
.pre-approval{position:absolute;top:643px;left:0;width:1200px;height:304px;background:var(--grey-bg);padding-top:38px}
.pre-approval p{text-align:center;font-size:16px;line-height:29px;color:var(--ink)}
.pre-approval .intro{margin-top:20px}
.pre-approval strong{font-weight:700;color:#111}

/* loans offered */
.loan-types{position:absolute;top:947px;left:0;width:1200px;height:548px;background:linear-gradient(90deg,#2c2f33 0%,#3a3c3f 45%,#4a4038 75%,#3a322d 100%);padding-top:30px}
.loan-types .section-title{color:var(--white)}
.loan-types .divider::before{border-color:rgba(255,255,255,.35)}
.loan-cards{position:absolute;left:162px;top:152px;display:flex;gap:21px}
.loan-card{width:203px;height:315px;background:var(--white);padding:14px 14px 0;text-align:center}
.loan-card .thumb{height:122px}
.loan-card h3{font-family:"Questrial",sans-serif;font-weight:700;color:var(--blue);font-size:21px;margin:18px 0 10px;letter-spacing:.3px}
.loan-card p{font-size:12px;line-height:18px;color:#333}
.read-more{display:inline-block;margin-top:16px;width:115px;height:29px;border:1px solid var(--blue);font-size:12px;font-weight:700;color:var(--blue);line-height:27px;border-left-width:3px;border-right-width:3px}

/* calculator */
.calc-band{position:absolute;top:1495px;left:0;width:1200px;height:189px;background:var(--white)}
.calc-band h2{position:absolute;left:162px;top:50px;font-size:42px;font-weight:700;color:var(--blue)}
.calc-band p{position:absolute;left:162px;top:107px;font-size:18px;font-weight:700;color:var(--ink)}
.calc-btn{position:absolute;left:807px;top:61px;width:195px;height:52px;background:var(--blue);color:var(--white);font-size:16px;font-weight:700;display:flex;align-items:center;justify-content:center;border-left:3px solid var(--blue-dark);border-right:3px solid var(--blue-dark)}

/* guarantee */
.guarantee-band{position:absolute;top:1684px;left:0;width:1200px;height:187px;background:linear-gradient(90deg,#6b4a33 0%,#3d3530 25%,#2b2a2b 60%,#3a3430 100%)}
.guarantee-band h2{position:absolute;left:162px;top:51px;font-size:26px;font-weight:400;color:var(--white)}
.guarantee-band p{position:absolute;left:162px;top:107px;font-size:18px;font-weight:700;color:var(--white)}
.guarantee-btn{position:absolute;left:807px;top:66px;width:195px;height:52px;background:var(--pale);color:var(--blue);font-size:16px;font-weight:700;display:flex;align-items:center;justify-content:center;border-left:3px solid var(--blue);border-right:3px solid var(--blue)}

/* footer */
.site-footer{position:absolute;top:1871px;left:0;width:1200px;height:312px;background:var(--blue);color:var(--white)}
.footer-col{position:absolute;top:28px}
.footer-col h4{font-size:18px;font-weight:700;letter-spacing:1px;text-transform:uppercase;padding-bottom:8px;border-bottom:1px solid rgba(255,255,255,.25);display:inline-block;padding-right:18px}
.quick-links{left:162px}
.quick-links ul{list-style:none;margin-top:8px}
.quick-links li{font-size:14px;line-height:30.5px;padding-left:13px;position:relative}
.quick-links li::before{content:"";position:absolute;left:0;top:12px;border:4px solid transparent;border-left:5px solid var(--white);border-right:0}
.quick-links li.is-current{color:#b9cde3}
.contact-details{left:377px}
.contact-row{display:flex;gap:14px;font-size:14px;line-height:20px;margin-top:14px}
.contact-row svg{flex:0 0 auto;margin-top:2px}
.contact-row.first{margin-top:20px}
.follow-us{left:673px}
.follow-us ul{list-style:none;margin-top:14px}
.follow-us li{display:flex;align-items:center;gap:12px;font-size:14px;height:48px}
.follow-us .icon{width:24px;height:24px;border-radius:3px;background:rgba(255,255,255,.85)}
.footer-mark{position:absolute;left:868px;top:70px;width:170px;height:170px;border-radius:50%;background:rgba(255,255,255,.12)}
.copyright{position:absolute;top:2183px;left:0;width:1200px;height:45px;background:var(--footer-bottom);color:var(--white);font-size:13px;text-align:center;line-height:45px}
</style>
</head>
<body>

<header class="site-header">
  <div class="brand"><span class="brand-dot"></span><span class="brand-name">Brightpath Finance</span></div>
  <div class="apply-btn">APPLY NOW</div>
  <div class="header-phone">
    <svg width="20" height="20" viewBox="0 0 24 24"><path fill="#222" d="M6.6 10.8a15.2 15.2 0 0 0 6.6 6.6l2.2-2.2c.3-.3.7-.4 1-.2 1.1.4 2.3.6 3.6.6.6 0 1 .4 1 1V20c0 .6-.4 1-1 1A17 17 0 0 1 3 4c0-.6.4-1 1-1h3.5c.6 0 1 .4 1 1 0 1.3.2 2.5.6 3.6.1.3 0 .7-.2 1z"/></svg>
    123-456-7890
  </div>
</header>

<nav class="main-nav">
  <ul>
    <li class="is-active">Home</li>
    <li>About Us</li>
    <li>Vehicle Loans</li>
    <li>Other Loans</li>
    <li>Insurance</li>
    <li>Finance Calculator</li>
    <li>Contact Us</li>
  </ul>
</nav>

<section class="hero">
  <div class="hero-photo" role="img" aria-label="Smiling finance consultant holding out car keys in a bright car showroom"></div>
  <ul class="rate-list">
    <li><svg width="17" height="14" viewBox="0 0 17 14"><path d="M1.5 7.5l4.5 4.5 9.5-10" fill="none" stroke="#111" stroke-width="3"/></svg>Low rate car loans from 4.69%<br>Comparison rate 4.99%*</li>
    <li><svg width="17" height="14" viewBox="0 0 17 14"><path d="M1.5 7.5l4.5 4.5 9.5-10" fill="none" stroke="#111" stroke-width="3"/></svg>Low fees</li>
    <li><svg width="17" height="14" viewBox="0 0 17 14"><path d="M1.5 7.5l4.5 4.5 9.5-10" fill="none" stroke="#111" stroke-width="3"/></svg>Low total cost loans</li>
  </ul>
  <form class="quote-panel">
    <div class="quote-title">QUICK &amp; EASY QUOTE</div>
    <div class="quote-field">First Name*</div>
    <div class="quote-field">Last Name*</div>
    <div class="quote-field">Email Address*</div>
    <div class="quote-field">Phone Number*</div>
    <div class="quote-field">Loan Amount in dollars *</div>
    <div class="quote-terms"><span class="box"></span>I agree to the <a>Terms &amp; Conditions</a></div>
    <div class="quote-submit">Get my best rate now</div>
  </form>
</section>

<section class="pre-approval">
  <h2 class="section-title">Online Loan Pre Approval</h2>
  <div class="divider"><span></span></div>
  <p class="intro">Complete our short online application to get finance for your car, truck, motorbike, equipment, boat or caravan!<br>
  We have helped thousands of Australians obtain the finance they need to buy a new or used vehicle.<br>
  <strong>We'll find you competitive vehicle finance that'll get you on the road fast and if you've had credit issues in the past,<br>
  we also have access to specialist lenders who could help.</strong></p>
</section>

<section class="loan-types" role="img" aria-label="Family smiling in front of their new home at dusk">
  <h2 class="section-title">We Offer Loans For</h2>
  <div class="divider"><span></span></div>
  <div class="loan-cards">
    <article class="loan-card">
      <div class="thumb" role="img" aria-label="Couple shaking hands with a car dealer" style="background:linear-gradient(135deg,#8a9aa8,#d7dde2)"></div>
      <h3>Vehicle Loans</h3>
      <p>Lorem ipsum dolor sit amet,<br>consectetur adipiscing elit.<br>Integer vitae interdum mi</p>
      <span class="read-more">Read More</span>
    </article>
    <article class="loan-card">
      <div class="thumb" role="img" aria-label="White motor yacht on blue water" style="background:linear-gradient(180deg,#4f8fd4,#1c4f8c)"></div>
      <h3>Boat Loans</h3>
      <p>Lorem ipsum dolor sit amet,<br>consectetur adipiscing elit.<br>Integer vitae interdum mi</p>
      <span class="read-more">Read More</span>
    </article>
    <article class="loan-card">
      <div class="thumb" role="img" aria-label="Model house on building plans with a calculator" style="background:linear-gradient(135deg,#c79a6a,#e8d8c0)"></div>
      <h3>Home Loans</h3>
      <p>Lorem ipsum dolor sit amet,<br>consectetur adipiscing elit.<br>Integer vitae interdum mi</p>
      <span class="read-more">Read More</span>
    </article>
    <article class="loan-card">
      <div class="thumb" role="img" aria-label="Couple meeting a financial adviser at a desk" style="background:linear-gradient(135deg,#5d5048,#c8c2bb)"></div>
      <h3>Personal Loans</h3>
      <p>Lorem ipsum dolor sit amet,<br>consectetur adipiscing elit.<br>Integer vitae interdum mi</p>
      <span class="read-more">Read More</span>
    </article>
  </div>
</section>

<section class="calc-band">
  <h2>What will my repayments be?</h2>
  <p>See how much you could borrow with our loan calculator.</p>
  <div class="calc-btn">LOAN CALCULATOR</div>
</section>

<section class="guarantee-band" role="img" aria-label="Small model house on a table, softly blurred background">
  <h2>Find out what Guaranteed Approval actually means</h2>
  <p>We explain what it means and what we offer instead.</p>
  <div class="guarantee-btn">FIND OUT MORE</div>
</section>

<footer class="site-footer">
  <div class="footer-col quick-links">
    <h4>Quick Links</h4>
    <ul>
      <li class="is-current">Home</li>
      <li>About Us</li>
      <li>Vehicle Loans</li>
      <li>Other Loans</li>
      <li>Insurance</li>
      <li>Finance Calculator</li>
      <li>Contact us</li>
    </ul>
  </div>
  <div class="footer-col contact-details">
    <h4>Contact Details</h4>
    <div class="contact-row first">
      <svg width="14" height="20" viewBox="0 0 14 20"><path fill="#fff" d="M7 0a7 7 0 0 0-7 7c0 5 7 13 7 13s7-8 7-13a7 7 0 0 0-7-7zm0 10a3 3 0 1 1 0-6 3 3 0 0 1 0 6z"/></svg>
      <span>Company Name<br>Street Name, City Name<br>State Name - 123456</span>
    </div>
    <div class="contact-row" style="margin-top:22px">
      <svg width="16" height="16" viewBox="0 0 24 24"><path fill="#fff" d="M6.6 10.8a15.2 15.2 0 0 0 6.6 6.6l2.2-2.2c.3-.3.7-.4 1-.2 1.1.4 2.3.6 3.6.6.6 0 1 .4 1 1V20c0 .6-.4 1-1 1A17 17 0 0 1 3 4c0-.6.4-1 1-1h3.5c.6 0 1 .4 1 1 0 1.3.2 2.5.6 3.6.1.3 0 .7-.2 1z"/></svg>
      <span>123-456-7890</span>
    </div>
    <div class="contact-row" style="margin-top:23px">
      <svg width="18" height="16" viewBox="0 0 18 16"><rect x="4" y="0" width="10" height="4" fill="#fff"/><rect x="0" y="5" width="18" height="7" rx="1" fill="#fff"/><rect x="4" y="10" width="10" height="6" fill="#fff" stroke="#0255a3" stroke-width="1"/></svg>
      <span>123-456-7890</span>
    </div>
    <div class="contact-row" style="margin-top:23px">
      <svg width="16" height="12" viewBox="0 0 16 12"><rect width="16" height="12" fill="#fff"/><path d="M0 0l8 6 8-6" fill="none" stroke="#0255a3" stroke-width="1.3"/></svg>
      <span>info@brightpathfinance.example.com</span>
    </div>
  </div>
  <div class="footer-col follow-us">
    <h4>Follow Us</h4>
    <ul>
      <li><span class="icon"></span>Friendwall</li>
      <li><span class="icon"></span>Chirpline</li>
      <li><span class="icon"></span>Worklink</li>
      <li><span class="icon"></span>Circleplus</li>
    </ul>
  </div>
  <div class="footer-mark"></div>
</footer>
<div class="copyright">Copyright © 2016 &nbsp;Brightpath Finance. All Right Reserved</div>

</body>
</html>
```